Stationary and email footer design using existing Logo design

Using the Logo design I currently have I need now to have this applied to all stationary requirements including email footer, Letter Head and footer, envelopes both window and non window ( standard letter size ).
You previously did the Logo and business cards so that's good.

```html
<!DOCTYPE html>
<html lang="en">
<head>
<meta charset="utf-8">
<title>Harbourline Advisory — Letterhead</title>
<link rel="stylesheet" href="https://fonts.googleapis.com/css2?family=Arimo:wght@400;700&family=Cinzel:wght@400&display=swap">
<style>
  :root {
    --backdrop: #dfe2e4;
    --paper: #ffffff;
    --brand-purple: #7c5aa8;
    --band-grey: #a3a3a3;
    --rule-grey: #c9c9c9;
    --body-text: #5b5b5b;
    --signature-tone: #eeeeee;
  }
  * { margin: 0; padding: 0; box-sizing: border-box; }
  html, body {
    width: 1200px; height: 784px; overflow: hidden;
    background: var(--backdrop);
  }
  .letterhead {
    position: absolute; left: 338px; top: 22px;
    width: 524px; height: 740px;
    background: var(--paper);
    box-shadow: 0 2px 10px rgba(0,0,0,0.12);
    overflow: hidden;
  }
  .header-rules { position: absolute; left: 0; top: 0; }
  .brand-name {
    position: absolute; left: 210px; top: 40px;
    font-family: "Arimo", sans-serif; font-weight: 700;
    font-size: 20px; color: var(--brand-purple);
    white-space: nowrap;
  }
  .letter-body {
    position: absolute; left: 78px; top: 118px; width: 372px;
    font-family: "Arimo", sans-serif; font-size: 9.2px;
    line-height: 1.45; color: var(--body-text);
  }
  .letter-body p { text-indent: 14px; margin-bottom: 11px; }
  .signature-area {
    position: absolute; left: 52px; top: 505px;
    width: 130px; height: 42px; background: var(--signature-tone);
  }
  .tagline {
    position: absolute; left: 40px; top: 598px;
    font-family: "Cinzel", serif; font-weight: 400;
    font-size: 10.5px; color: var(--brand-purple); letter-spacing: 0.3px;
    white-space: nowrap;
  }
  .contact-line {
    position: absolute; left: 40px; top: 616px;
    display: flex; align-items: center; gap: 5px;
    font-family: "Arimo", sans-serif; font-size: 7.4px; color: var(--body-text);
    white-space: nowrap;
  }
  .contact-line svg { flex: none; }
  .footer-bands { position: absolute; left: 0; bottom: 0; }
  .web-address {
    position: absolute; right: 22px; bottom: 18px;
    font-family: "Arimo", sans-serif; font-weight: 700;
    font-size: 12px; color: var(--paper); white-space: nowrap;
  }
</style>
</head>
<body>
  <main class="letterhead">
    <svg class="header-rules" width="524" height="90" viewBox="0 0 524 90" aria-hidden="true">
      <rect x="0" y="44" width="196" height="6" fill="var(--brand-purple)"/>
      <rect x="0" y="52" width="196" height="1.5" fill="var(--rule-grey)"/>
      <rect x="384" y="70" width="86" height="7" fill="var(--band-grey)"/>
      <rect x="384" y="79" width="86" height="1.5" fill="var(--rule-grey)"/>
    </svg>
    <div class="brand-name">Harbourline Advisory</div>

    <section class="letter-body">
      <p>Lorem ipsum dolor sit amet, consectetur adipiscing elit, sed do eiusmod tempor incididunt ut labore et dolore magna aliqua. Ut enim ad minim veniam, quis nostrud exercitation ullamco laboris nisi ut aliquip ex ea commodo consequat. Duis aute irure dolor in reprehenderit in voluptate velit esse cillum dolore eu fugiat nulla pariatur. Excepteur sint occaecat cupidatat non proident, sunt in culpa qui officia deserunt mollit anim id est laborum, sed ut perspiciatis unde omnis iste natus error sit voluptatem accusantium doloremque laudantium.</p>
      <p>Totam rem aperiam, eaque ipsa quae ab illo inventore veritatis et quasi architecto beatae vitae dicta sunt explicabo. Nemo enim ipsam voluptatem quia voluptas sit aspernatur aut odit aut fugit, sed quia consequuntur magni dolores eos qui ratione voluptatem sequi nesciunt. Neque porro quisquam est, qui dolorem ipsum quia dolor sit amet, consectetur, adipisci velit, sed quia non numquam eius modi tempora incidunt ut labore et dolore magnam aliquam quaerat voluptatem.</p>
      <p>Ut enim ad minima veniam, quis nostrum exercitationem ullam corporis suscipit laboriosam, nisi ut aliquid ex ea commodi consequatur. Quis autem vel eum iure reprehenderit qui in ea voluptate velit esse quam nihil molestiae consequatur, vel illum qui dolorem eum fugiat quo voluptas nulla pariatur. At vero eos et accusamus et iusto odio dignissimos ducimus qui blanditiis praesentium voluptatum deleniti atque corrupti quos dolores et quas molestias excepturi sint occaecati cupiditate non provident, similique sunt in culpa.</p>
    </section>

    <div class="signature-area" role="img" aria-label="Handwritten signature of the sender"></div>

    <div class="tagline">Planning beside you for a steadier tomorrow</div>
    <div class="contact-line">
      <svg width="8" height="8" viewBox="0 0 8 8" aria-hidden="true"><circle cx="4" cy="4" r="4" fill="var(--brand-purple)"/><circle cx="4" cy="3.4" r="1.3" fill="#fff"/></svg>
      <span>Unit 4, Level 2 Harbour Court 12 Wattle Street, Seaview WA 6100</span>
      <svg width="8" height="8" viewBox="0 0 8 8" aria-hidden="true"><circle cx="4" cy="4" r="4" fill="var(--brand-purple)"/><rect x="3" y="2" width="2" height="4" rx="0.6" fill="#fff"/></svg>
      <span>08 5550 7312</span>
      <svg width="8" height="8" viewBox="0 0 8 8" aria-hidden="true"><circle cx="4" cy="4" r="4" fill="var(--brand-purple)"/><rect x="2" y="2.6" width="4" height="2.8" fill="#fff"/></svg>
      <span>hello@harbourline.com.au</span>
    </div>

    <svg class="footer-bands" width="524" height="100" viewBox="0 0 524 100" aria-hidden="true">
      <rect x="0" y="42" width="348" height="1.5" fill="var(--rule-grey)"/>
      <rect x="0" y="46" width="300" height="6" fill="var(--brand-purple)"/>
      <polygon points="300,46 320,46 340,64 320,64" fill="var(--brand-purple)"/>
      <rect x="0" y="58" width="310" height="1.5" fill="var(--rule-grey)"/>
      <polygon points="334,60 524,60 524,100 374,100" fill="var(--brand-purple)"/>
    </svg>
    <div class="web-address">www.harbourline.com.au</div>
  </main>
</body>
</html>
```